Goodlooking website for a company who is working in the IT consultancy

We want a new website designed in WordPress. You can take www.vantoro.nl as an example. It should be a website with some short blocks of information about the company, nice pictures of our partners and our employees. A job page with a clear filter.

Target Market(s)

B2B

Industry/Entity Type

It Company

Coding

Coded - Design and coding required

Number of Pages Required

5+ page

Font styles to use
Sans Serif

Colors
0455a3
34a7d8

Requirements
Must have
• Check briefing

```html
<!DOCTYPE html>
<html lang="en">
<head>
<meta charset="utf-8">
<title>Velora – Connecting IT-Professionals</title>
<link href="https://fonts.googleapis.com/css2?family=Montserrat:wght@400;600;700&family=Open+Sans:wght@400;600;700&display=swap" rel="stylesheet">
<style>
:root{
  --blue:#1b9bd1;
  --blue-dark:#0455a3;
  --green:#17a88e;
  --ink:#1f2a33;
  --text:#4a4f55;
  --grey-bg:#efefef;
  --hero-bg:#ececec;
  --line:#d6d6d6;
  --icon-dark:#3a4550;
  --footer:#2e3842;
  --footer-text:#c9cfd4;
  --partner:#6d747b;
  --white:#ffffff;
}
*{box-sizing:border-box;margin:0;padding:0}
html,body{width:1200px;height:3644px;overflow:hidden}
body{position:relative;background:var(--white);font-family:"Open Sans",Arial,sans-serif;color:var(--text)}
.abs{position:absolute}
.section-title{position:absolute;left:0;width:1200px;text-align:center;font-family:"Montserrat",Arial,sans-serif;font-weight:700;font-size:22px;color:var(--ink);letter-spacing:.5px}
.section-rule{position:absolute;left:575px;width:50px;height:4px;background:var(--line);border-radius:2px}
.btn{position:absolute;display:flex;align-items:center;justify-content:center;background:var(--blue);color:var(--white);font-family:"Montserrat",Arial,sans-serif;font-weight:700;font-size:12px;letter-spacing:.5px;border-radius:3px}

/* header + hero */
.hero{position:absolute;left:0;top:0;width:1200px;height:635px;background:radial-gradient(ellipse at 50% 35%,#fafafa 0%,var(--hero-bg) 70%)}
.brand{position:absolute;display:flex;align-items:center;gap:14px;font-family:"Montserrat",Arial,sans-serif;font-weight:700;color:var(--ink)}
.brand-dot{border-radius:50%;background:var(--blue)}
.call{position:absolute;left:898px;top:26px;display:flex;align-items:center;gap:12px}
.call-icon{width:28px;height:28px;border-radius:50%;background:var(--green);display:flex;align-items:center;justify-content:center}
.call-label{font-family:"Montserrat",Arial,sans-serif;font-size:11px;font-weight:700;color:var(--ink)}
.call-number{font-family:"Montserrat",Arial,sans-serif;font-size:22px;font-weight:700;color:var(--green);line-height:1}
.nav{position:absolute;top:78px;left:624px;display:flex;gap:28px;font-family:"Montserrat",Arial,sans-serif;font-size:12px;font-weight:600;color:var(--ink);letter-spacing:.3px}
.nav a{color:inherit;text-decoration:none;padding:5px 0}
.nav a.active{background:var(--blue);color:var(--white);padding:5px 10px;margin-right:-6px}
.hero-title{position:absolute;top:176px;width:1200px;text-align:center;font-family:"Montserrat",Arial,sans-serif;font-weight:700;font-size:26px;color:var(--ink)}
.hero-title span{color:var(--green)}
.hero-sub{position:absolute;top:214px;width:1200px;text-align:center;font-size:14px;color:var(--ink)}
.hero-photo{position:absolute;left:0;top:340px;width:1200px;height:295px;background:linear-gradient(90deg,#5c6470 0%,#3f6fae 14%,#d9a928 32%,#c65233 50%,#3a3f4a 62%,#9b3b44 78%,#46607e 100%)}
.dots{position:absolute;top:571px;left:548px;display:flex;gap:14px}
.dots i{width:9px;height:9px;border-radius:50%;background:var(--white);display:block}
.dots i.on{background:var(--blue)}

/* what we do */
.diag{position:absolute;left:0;top:1220px}
.service-title{position:absolute;width:260px;text-align:center;font-family:"Montserrat",Arial,sans-serif;font-weight:600;font-size:14px;color:var(--ink)}
.service-text{position:absolute;width:200px;text-align:center;font-size:11px;line-height:1.4;color:var(--text)}
.service-link{position:absolute;overflow:visible}
.icon-box{filter:drop-shadow(0 3px 5px rgba(0,0,0,.18))}

/* about */
.about{position:absolute;left:0;top:1290px;width:1200px;height:568px;background:var(--grey-bg)}
.about-label{position:absolute;left:284px;top:1404px;font-family:"Montserrat",Arial,sans-serif;font-weight:700;font-size:20px;color:var(--ink)}
.about-name{position:absolute;left:284px;top:1432px;font-family:"Montserrat",Arial,sans-serif;font-weight:700;font-size:36px;letter-spacing:4px;color:var(--ink)}
.about-text{position:absolute;left:284px;top:1515px;width:336px;font-size:11px;line-height:1.45;text-align:justify;color:var(--text)}

/* jobs */
.job-card{position:absolute;top:2056px;width:224px;height:296px;background:var(--white);border:1px solid #e3e3e3;box-shadow:0 1px 4px rgba(0,0,0,.06);padding:22px 20px 0 20px}
.job-head{display:flex;gap:12px}
.job-chev{color:var(--ink);font-weight:700;font-size:16px;line-height:1}
.job-title{font-family:"Montserrat",Arial,sans-serif;font-weight:700;font-size:13px;color:var(--ink);line-height:1.3}
.job-company{font-size:11px;color:var(--text);margin-top:4px}
.job-text{margin:16px 0 0 30px;font-size:11.5px;line-height:1.45;color:var(--text)}
.job-apply{display:inline-block;margin:14px 0 0 30px;background:var(--blue);color:var(--white);font-family:"Montserrat",Arial,sans-serif;font-weight:700;font-size:9px;padding:4px 8px;border-radius:2px}
.slider-arrow{position:absolute;top:2196px;font-size:26px;color:#8a8f95}

/* contact */
.contact{position:absolute;left:0;top:2442px;width:1200px;height:474px;background:var(--grey-bg)}
.info-item{position:absolute;display:flex;gap:16px}
.info-icon{width:42px;height:42px;border-radius:50%;background:var(--blue);display:flex;align-items:center;justify-content:center;flex:none}
.info-label{font-family:"Montserrat",Arial,sans-serif;font-weight:700;font-size:12px;color:var(--blue);margin-top:4px}
.info-value{font-size:12px;color:var(--ink);line-height:1.45;margin-top:4px}
.field{position:absolute;background:var(--white);border:1px solid #cfd4d8;border-radius:3px;font-size:11px;color:var(--ink);padding:9px 12px}

/* partners */
.partner{position:absolute;top:3142px;display:flex;align-items:center;gap:10px;font-family:"Montserrat",Arial,sans-serif;font-weight:600;font-size:22px;color:var(--partner);white-space:nowrap}
.partner-mark{width:18px;height:18px;border-radius:3px;flex:none}

/* footer */
.footer{position:absolute;left:0;top:3280px;width:1200px;height:364px;background:var(--footer)}
.foot-head{position:absolute;font-family:"Montserrat",Arial,sans-serif;font-weight:700;font-size:12px;color:var(--white);letter-spacing:.3px}
.foot-list{position:absolute;font-size:11.5px;line-height:1.55;color:var(--footer-text);list-style:none}
.social{position:absolute;display:flex;flex-direction:column;gap:18px;font-size:11.5px;color:var(--footer-text)}
.social li{list-style:none;display:flex;align-items:center;gap:10px}
.social i{width:24px;height:24px;border-radius:50%;display:block}
.copyright{position:absolute;top:3595px;width:1200px;text-align:center;font-size:11.5px;color:var(--footer-text)}
</style>
</head>
<body>

<!-- header + hero -->
<header class="hero">
  <div class="brand" style="left:134px;top:30px;font-size:34px;letter-spacing:3px">
    <span class="brand-dot" style="width:66px;height:66px"></span>VELORA
  </div>
  <div class="call">
    <span class="call-icon">
      <svg width="14" height="14" viewBox="0 0 24 24"><path fill="#fff" d="M6.6 10.8a15 15 0 0 0 6.6 6.6l2.2-2.2c.3-.3.7-.4 1-.2 1.1.4 2.3.6 3.6.6.6 0 1 .4 1 1V20c0 .6-.4 1-1 1A17 17 0 0 1 3 4c0-.6.4-1 1-1h3.5c.6 0 1 .4 1 1 0 1.3.2 2.5.6 3.6.1.3 0 .7-.2 1z"/></svg>
    </span>
    <div><div class="call-label">CALL US</div><div class="call-number">085-3174460</div></div>
  </div>
  <nav class="nav">
    <a class="active">HOME</a><a>OUR SOLUTIONS</a><a>OUR TEAM</a><a>JOB</a><a>CONTACT US</a>
  </nav>
  <h1 class="hero-title">CONNECTING <span>IT-PROFESSIONALS</span></h1>
  <p class="hero-sub">Sed ut perspiciatis unde omnis iste natus error sit volup</p>
  <div class="btn" style="left:547px;top:262px;width:107px;height:30px">READ MORE</div>
  <div class="hero-photo" role="img" aria-label="Photo of a team of colleagues standing arm in arm, seen from behind"></div>
  <div class="dots"><i></i><i class="on"></i><i></i><i></i><i></i></div>
</header>

<!-- what we do -->
<h2 class="section-title" style="top:700px">WHAT WE DO</h2>
<div class="section-rule" style="top:746px"></div>

<svg class="diag" width="1200" height="80" viewBox="0 0 1200 80"><polygon points="0,80 1200,0 1200,80" fill="#efefef"/></svg>

<section class="about"></section>

<!-- Training -->
<div class="service-title" style="left:101px;top:906px">Training</div>
<p class="service-text" style="left:131px;top:940px">Sed ut perspiciatis unde omnis iste natus error sit voluptatem accusantium doloremque laudantium.</p>
<svg class="service-link" style="left:141px;top:1010px" width="180" height="290" viewBox="0 0 180 290">
  <g stroke="#2b3440" stroke-width="3" fill="none">
    <path d="M22 0V50" stroke-dasharray="6 6"/><path d="M158 0V50" stroke-dasharray="6 6"/>
    <path d="M22 50V130Q22 165 90 165Q158 165 158 130V50"/><path d="M90 165V270"/>
  </g>
  <circle cx="90" cy="165" r="5" fill="#2b3440"/>
  <circle cx="90" cy="278" r="8" fill="#fff" stroke="#2b3440" stroke-width="3"/>
  <rect class="icon-box" x="35" y="30" width="110" height="110" rx="14" fill="#fff"/>
  <g fill="none" stroke="#3a4550" stroke-width="4" stroke-linecap="round" stroke-linejoin="round">
    <rect x="66" y="62" width="48" height="34" rx="2"/>
    <path d="M80 96L72 114M100 96L108 114M90 96V110"/>
    <path d="M74 88L86 78L94 84L106 70"/>
  </g>
</svg>

<!-- Personal Coaching -->
<div class="service-title" style="left:344px;top:831px">Personal Coaching</div>
<p class="service-text" style="left:374px;top:865px">Sed ut perspiciatis unde omnis iste natus error sit voluptatem accusantium doloremque laudantium.</p>
<svg class="service-link" style="left:384px;top:937px" width="180" height="340" viewBox="0 0 180 340">
  <g stroke="#1b9bd1" stroke-width="3" fill="none">
    <path d="M22 0V50" stroke-dasharray="6 6"/><path d="M158 0V50" stroke-dasharray="6 6"/>
    <path d="M22 50V130Q22 165 90 165Q158 165 158 130V50"/><path d="M90 165V322"/>
  </g>
  <circle cx="90" cy="165" r="5" fill="#1b9bd1"/>
  <circle cx="90" cy="330" r="8" fill="#fff" stroke="#1b9bd1" stroke-width="3"/>
  <rect class="icon-box" x="35" y="30" width="110" height="110" rx="14" fill="#fff"/>
  <g fill="none" stroke="#1b9bd1" stroke-width="4" stroke-linecap="round">
    <path d="M62 62H118"/>
    <rect x="66" y="62" width="48" height="36" rx="2"/>
    <path d="M90 98V112M80 114L90 108L100 114"/>
  </g>
  <g fill="#1b9bd1">
    <rect x="75" y="82" width="6" height="10"/><rect x="86" y="76" width="6" height="16"/><rect x="97" y="70" width="6" height="22"/>
  </g>
</svg>

<!-- Education Projects -->
<div class="service-title" style="left:589px;top:913px">Education Projects</div>
<p class="service-text" style="left:619px;top:947px">Sed ut perspiciatis unde omnis iste natus error sit voluptatem accusantium doloremque laudantium.</p>
<svg class="service-link" style="left:629px;top:1015px" width="180" height="250" viewBox="0 0 180 250">
  <g stroke="#2b3440" stroke-width="3" fill="none">
    <path d="M22 0V50" stroke-dasharray="6 6"/><path d="M158 0V50" stroke-dasharray="6 6"/>
    <path d="M22 50V130Q22 165 90 165Q158 165 158 130V50"/><path d="M90 165V233"/>
  </g>
  <circle cx="90" cy="165" r="5" fill="#2b3440"/>
  <circle cx="90" cy="241" r="8" fill="#fff" stroke="#2b3440" stroke-width="3"/>
  <rect class="icon-box" x="35" y="30" width="110" height="110" rx="14" fill="#fff"/>
  <rect x="68" y="56" width="44" height="58" rx="3" fill="#3a4550"/>
  <rect x="68" y="56" width="7" height="58" fill="#2b3440"/>
  <path d="M82 68H104M82 74H104" stroke="#fff" stroke-width="2"/>
</svg>

<!-- Cloud Consultancy -->
<div class="service-title" style="left:840px;top:831px">Cloud Consultancy</div>
<p class="service-text" style="left:870px;top:865px">Sed ut perspiciatis unde omnis iste natus error sit voluptatem accusantium doloremque laudantium.</p>
<svg class="service-link" style="left:880px;top:937px" width="180" height="320" viewBox="0 0 180 320">
  <g stroke="#17a88e" stroke-width="3" fill="none">
    <path d="M22 0V50" stroke-dasharray="6 6"/><path d="M158 0V50" stroke-dasharray="6 6"/>
    <path d="M22 50V130Q22 165 90 165Q158 165 158 130V50"/><path d="M90 165V298"/>
  </g>
  <circle cx="90" cy="165" r="5" fill="#17a88e"/>
  <circle cx="90" cy="306" r="8" fill="#fff" stroke="#17a88e" stroke-width="3"/>
  <rect class="icon-box" x="35" y="30" width="110" height="110" rx="14" fill="#fff"/>
  <path d="M70 104H112A14 14 0 0 0 110 76A20 20 0 0 0 72 80A12 12 0 0 0 70 104Z" fill="#17a88e"/>
  <g fill="none" stroke="#fff" stroke-width="3" stroke-linecap="round">
    <path d="M81 88A10 10 0 0 1 99 86"/><path d="M99 94A10 10 0 0 1 81 96"/>
  </g>
  <path d="M96 80L102 87L94 89Z M84 104L78 97L86 95Z" fill="#fff"/>
</svg>

<!-- about -->
<span class="abs" style="left:170px;top:1410px;width:76px;height:76px;border-radius:50%;background:var(--blue)"></span>
<div class="about-label">ABOUT</div>
<div class="about-name">VELORA</div>
<p class="about-text">But I must explain to you how all this mistaken idea of denouncing pleasure and praising pain was born and I will give you a complete account of the system, and expound the actual teachings of the great explorer of the truth, the master-builder of human happiness. No one rejects, dislikes, or avoids pleasure itself, because it is pleasure, but because those who do not know how to pursue pleasure rationally encounter</p>
<div class="btn" style="left:284px;top:1691px;width:110px;height:30px">READ MORE</div>
<svg class="abs" style="left:648px;top:1380px" width="384" height="384" viewBox="-4 -4 394 394" role="img" aria-label="Photos of people working at laptops, arranged as a circle in four quarters">
  <defs>
    <linearGradient id="q1" x1="0" y1="0" x2="1" y2="1"><stop offset="0" stop-color="#a9d6d8"/><stop offset="1" stop-color="#3f8f99"/></linearGradient>
    <linearGradient id="q2" x1="0" y1="0" x2="1" y2="1"><stop offset="0" stop-color="#cfd8dc"/><stop offset="1" stop-color="#8fa3ad"/></linearGradient>
    <linearGradient id="q3" x1="0" y1="0" x2="1" y2="1"><stop offset="0" stop-color="#6f7a82"/><stop offset="1" stop-color="#b9c3c8"/></linearGradient>
    <linearGradient id="q4" x1="0" y1="0" x2="1" y2="1"><stop offset="0" stop-color="#8cc8d8"/><stop offset="1" stop-color="#4ea0b8"/></linearGradient>
  </defs>
  <path d="M190 0A190 190 0 0 0 0 190H190Z" fill="url(#q1)"/>
  <path d="M196 0A190 190 0 0 1 386 190H196Z" fill="url(#q2)"/>
  <path d="M0 196A190 190 0 0 0 190 386V196Z" fill="url(#q3)"/>
  <path d="M196 196H386A190 190 0 0 1 196 386Z" fill="url(#q4)"/>
</svg>

<!-- jobs -->
<h2 class="section-title" style="top:1930px">JOBS</h2>
<div class="section-rule" style="top:1976px"></div>
<div class="slider-arrow" style="left:76px">&#8249;</div>
<div class="slider-arrow" style="left:1110px">&#8250;</div>

<article class="job-card" style="left:129px">
  <div class="job-head"><span class="job-chev">&raquo;</span><div><div class="job-title">Web Researcher/ Online Researcher</div><div class="job-company">Brightpath Systems</div></div></div>
  <p class="job-text">But I must explain to you how all this mistaken idea of den ouncing pleasure and praising pain was born and I will give you a complete account of the system, and expound the actual teachings of the great.</p>
  <span class="job-apply">APPLY JOB</span>
</article>
<article class="job-card" style="left:369px">
  <div class="job-head"><span class="job-chev">&raquo;</span><div><div class="job-title">Software Developer fresher 2017-2018</div><div class="job-company">Brightpath Systems</div></div></div>
  <p class="job-text">But I must explain to you how all this mistaken idea of den ouncing pleasure and praising pain was born and I will give you a complete account of the system, and expound the actual teachings of the great.</p>
  <span class="job-apply">APPLY JOB</span>
</article>
<article class="job-card" style="left:607px">
  <div class="job-head"><span class="job-chev">&raquo;</span><div><div class="job-title">Catalog Quality Associate, French</div><div class="job-company">Brightpath Systems</div></div></div>
  <p class="job-text">But I must explain to you how all this mistaken idea of den ouncing pleasure and praising pain was born and I will give you a complete account of the system, and expound the actual teachings of the great.</p>
  <span class="job-apply">APPLY JOB</span>
</article>
<article class="job-card" style="left:845px">
  <div class="job-head"><span class="job-chev">&raquo;</span><div><div class="job-title">Required candidates in Hollin company</div><div class="job-company">Brightpath Systems</div></div></div>
  <p class="job-text">But I must explain to you how all this mistaken idea of den ouncing pleasure and praising pain was born and I will give you a complete account of the system, and expound the actual teachings of the great.</p>
  <span class="job-apply">APPLY JOB</span>
</article>

<!-- contact -->
<section class="contact"></section>
<h2 class="section-title" style="top:2506px">CONTACT US</h2>
<div class="section-rule" style="top:2552px"></div>
<svg class="abs" style="left:146px;top:2624px" width="426" height="208"><line x1="250" y1="0" x2="250" y2="208" stroke="#d0d0d0"/><line x1="0" y1="112" x2="426" y2="112" stroke="#d0d0d0"/></svg>

<div class="info-item" style="left:166px;top:2645px">
  <span class="info-icon"><svg width="16" height="18" viewBox="0 0 24 24"><path fill="#fff" d="M12 2a7 7 0 0 0-7 7c0 5 7 13 7 13s7-8 7-13a7 7 0 0 0-7-7zm0 9.5A2.5 2.5 0 1 1 12 6.5a2.5 2.5 0 0 1 0 5z"/></svg></span>
  <div><div class="info-label">ADDRESS</div><div class="info-value">VELORA, Lindeplein 14<br>3521 KB Utrecht</div></div>
</div>
<div class="info-item" style="left:445px;top:2645px">
  <span class="info-icon"><svg width="16" height="16" viewBox="0 0 24 24"><path fill="#fff" d="M6.6 10.8a15 15 0 0 0 6.6 6.6l2.2-2.2c.3-.3.7-.4 1-.2 1.1.4 2.3.6 3.6.6.6 0 1 .4 1 1V20c0 .6-.4 1-1 1A17 17 0 0 1 3 4c0-.6.4-1 1-1h3.5c.6 0 1 .4 1 1 0 1.3.2 2.5.6 3.6.1.3 0 .7-.2 1z"/></svg></span>
  <div><div class="info-label">TELEPHONE</div><div class="info-value">085-3174460</div></div>
</div>
<div class="info-item" style="left:166px;top:2760px">
  <span class="info-icon"><svg width="16" height="14" viewBox="0 0 24 20"><path fill="#fff" d="M2 2h20v16H2zm2 2v.5l8 5.5 8-5.5V4z"/></svg></span>
  <div><div class="info-label">MAIL:</div><div class="info-value">info@velora.nl</div></div>
</div>

<div class="field" style="left:641px;top:2644px;width:200px;height:36px">Name</div>
<div class="field" style="left:847px;top:2644px;width:200px;height:36px">E-mail</div>
<div class="field" style="left:641px;top:2689px;width:406px;height:86px">Message</div>
<div class="btn" style="left:641px;top:2794px;width:93px;height:33px">SUBMIT</div>

<!-- partners -->
<h2 class="section-title" style="top:2994px">PARTNERS</h2>
<div class="section-rule" style="top:3040px"></div>
<div class="partner" style="left:238px"><span class="partner-mark" style="background:#2496c9"></span>Harborly</div>
<div class="partner" style="left:432px"><span class="partner-mark" style="background:#7a7f85"></span>Corvane</div>
<div class="partner" style="left:650px"><span class="partner-mark" style="background:#1f5fa8"></span>Ironbit</div>
<div class="partner" style="left:838px;font-size:19px"><span class="partner-mark" style="background:#c9302c"></span>Scarlet Systems</div>

<!-- footer -->
<footer class="footer"></footer>
<div class="brand" style="left:134px;top:3380px;font-size:34px;letter-spacing:3px;color:#fff">
  <span class="brand-dot" style="width:70px;height:70px;background:#fff"></span>VELORA
</div>
<div class="foot-head" style="left:481px;top:3340px">LATEST NEWS</div>
<ul class="foot-list" style="left:481px;top:3372px">
  <li>Website Velora live!</li><li>Velora visited Corvane Tech Event.</li><li>Velora has become a Scarlet Systems partner.</li>
</ul>
<div class="foot-head" style="left:763px;top:3340px">MENU</div>
<ul class="foot-list" style="left:763px;top:3372px">
  <li>Home</li><li>Our solutions</li><li>Our team</li><li>Job</li><li>Contact Us</li>
</ul>
<div class="foot-head" style="left:935px;top:3340px">CONNECT WITH US</div>
<ul class="social" style="left:935px;top:3378px">
  <li><i style="background:#3b5c9c"></i>Chatterly</li>
  <li><i style="background:#2aa3e0"></i>Pinwire</li>
  <li><i style="background:#1c5f93"></i>Workweb</li>
</ul>
<svg class="abs" style="left:129px;top:3558px" width="942" height="2"><line x1="0" y1="1" x2="942" y2="1" stroke="#46515b"/></svg>
<p class="copyright">Copyrights @ 2018 All Rights Reserved</p>

</body>
</html>
```